Need Business Card for our Real Estate Business with Sales Executive's Picture

PANTONE 484 C ( RED)

PANTONE 2766 C ( BLUE

Industry/Entity Type

Real Estate

Contact Information for Business Card

Name, Mobile, email, & picture of Person
Agency Phone, address, Web address

Requirements
Must have
• Our Logo Colours, Agent Picture,

```html
<!DOCTYPE html>
<html lang="en">
<head>
<meta charset="utf-8">
<title>Dunmore Real Estate – Business Card</title>
<link rel="stylesheet" href="https://fonts.googleapis.com/css2?family=Open+Sans:wght@400;600&display=swap">
<style>
  :root {
    --backdrop: #cbced2;
    --card-white: #ffffff;
    --navy: #061538;
    --navy-flap: #6c7386;
    --brand-red: #9a3324;
    --text-grey: #4a4a4a;
    --icon-grey: #555555;
    --photo-top: #c9ccd6;
    --photo-bottom: #24337a;
  }
  * { margin: 0; padding: 0; box-sizing: border-box; }
  html, body {
    width: 1200px;
    height: 1000px;
    overflow: hidden;
    background: var(--backdrop);
    font-family: "Open Sans", Arial, sans-serif;
  }
  .canvas { position: relative; width: 1200px; height: 1000px; }

  .card { position: absolute; width: 680px; height: 388px; overflow: hidden; }
  .card-front { left: 262px; top: 85px; background: var(--card-white); }
  .card-back { left: 261px; top: 526px; background: var(--navy); }

  .agent-photo {
    position: absolute; left: 35px; top: 35px; width: 123px; height: 162px;
    background: linear-gradient(180deg, var(--photo-top) 0%, var(--photo-bottom) 100%);
  }

  .brand-name {
    position: absolute; left: 0; width: 100%; text-align: center;
    font-weight: 600; letter-spacing: 0.08em; line-height: 1;
  }
  .card-front .brand-name { top: 68px; left: 230px; width: 226px; font-size: 20px; color: var(--navy); }
  .card-back .brand-name {
    top: 220px; left: 0; font-size: 42px; color: var(--card-white);
    display: flex; justify-content: center; align-items: center; gap: 14px;
  }
  .brand-square { width: 14px; height: 14px; background: var(--brand-red); display: inline-block; }

  .divider-line { position: absolute; left: 0; top: 202px; width: 100%; height: 3px; background: var(--navy); }
  .title-ribbon { position: absolute; left: 163px; top: 176px; width: 364px; height: 40px; }
  .agent-name {
    position: absolute; left: 188px; top: 140px; width: 300px; text-align: center;
    font-size: 23px; color: var(--text-grey); white-space: nowrap;
  }
  .agent-title {
    position: absolute; left: 190px; top: 181px; width: 300px; text-align: center;
    font-size: 19px; color: var(--card-white);
  }
  .office-address {
    position: absolute; left: 0; top: 222px; width: 680px; padding-left: 0;
    text-align: center; font-size: 18px; color: var(--text-grey);
  }
  .office-address span { display: inline-block; margin-left: 0; transform: translateX(0); }

  .contact-list { position: absolute; left: 210px; top: 270px; list-style: none; }
  .contact-item {
    display: flex; align-items: center; height: 31px;
    font-size: 19px; color: var(--text-grey);
  }
  .contact-icon { width: 20px; height: 20px; margin-right: 24px; flex: none; }

  .back-cutout { position: absolute; left: 0; bottom: 0; width: 680px; height: 92px; }
</style>
</head>
<body>
<main class="canvas">

  <section class="card card-front" aria-label="Business card front">
    <div class="agent-photo" role="img" aria-label="Portrait photo of the sales executive"></div>
    <div class="brand-name">DUNMORE</div>

    <div class="agent-name">Name of Sales Executive's</div>
    <div class="divider-line"></div>
    <svg class="title-ribbon" viewBox="0 0 364 40" aria-hidden="true">
      <polygon points="0,26 8,2 20,2 16,26" fill="var(--navy-flap)"/>
      <polygon points="364,26 356,2 344,2 348,26" fill="var(--navy-flap)"/>
      <polygon points="8,2 356,2 346,38 18,38" fill="var(--navy)"/>
    </svg>
    <div class="agent-title">Sales Executive</div>

    <div class="office-address"><span>address of Dunmore Real Estate</span></div>

    <ul class="contact-list">
      <li class="contact-item">
        <svg class="contact-icon" viewBox="0 0 20 20" aria-hidden="true">
          <circle cx="10" cy="10" r="8" fill="none" stroke="var(--icon-grey)" stroke-width="1.6"/>
          <path d="M7 6.2c.5-.4 1-.3 1.3.2l.7 1.3c.2.4 0 .8-.3 1l-.4.3c.4 1 1.1 1.8 2 2.3l.4-.4c.3-.3.7-.3 1 0l1.2.9c.4.3.4.8 0 1.2-.6.7-1.5.9-2.4.5-2-.9-3.4-2.5-4.1-4.5-.3-1-.1-2.2.6-2.8z" fill="var(--icon-grey)"/>
        </svg>
        mobile / agency phone
      </li>
      <li class="contact-item">
        <svg class="contact-icon" viewBox="0 0 20 20" aria-hidden="true">
          <rect x="2" y="5" width="16" height="11" fill="var(--icon-grey)"/>
          <polyline points="2,5 10,11 18,5" fill="none" stroke="var(--card-white)" stroke-width="1.2"/>
        </svg>
        dunmore@email.com
      </li>
      <li class="contact-item">
        <svg class="contact-icon" viewBox="0 0 20 20" aria-hidden="true">
          <circle cx="10" cy="10" r="8" fill="var(--icon-grey)"/>
          <g fill="none" stroke="var(--card-white)" stroke-width="1">
            <ellipse cx="10" cy="10" rx="3.5" ry="8"/>
            <line x1="2" y1="10" x2="18" y2="10"/>
            <line x1="3.5" y1="6" x2="16.5" y2="6"/>
            <line x1="3.5" y1="14" x2="16.5" y2="14"/>
          </g>
        </svg>
        www.web address.com
      </li>
    </ul>
  </section>

  <section class="card card-back" aria-label="Business card back">
    <div class="brand-name"><span class="brand-square"></span>DUNMORE</div>
    <svg class="back-cutout" viewBox="0 0 680 92" aria-hidden="true">
      <path d="M95 92 C130 30 140 2 190 2 L490 2 C540 2 550 30 578 92 Z" fill="var(--card-white)"/>
    </svg>
  </section>

</main>
</body>
</html>
```